Corvane Lending Partners. Professional and Established Company

A full service finance company specializing in obtaining capital for small business. Business Lending advisor, helping small business owners access the capital they need to launch, grow, or sustain their business. Many of our programs offer flexible guidelines to overcome common obstacles such as credit score, credit history, and time in business, financials, and industry type. Our streamlined funding process makes getting a business loan, business line of credit, stated income commercial real estate loan, a smooth and stress free experience.SOME OF THE MOST COMMON NEEDS FOR BUSINESS CAPITAL:• Working Capital• Debt Consolidations (loans, merchant cash advances, etc.)• Payroll• Operating Expenses• Inventory• Equipment Financing• Commercial Real Estate (Purchase, Fix & Flip, Rehab, Renovations)• Business Acquisitions• Business ExpansionWe like the websites:www.quillmorecf.com they are in the same industry and provide the same servicesWe are wanting to be able to update when we do press releases and such using Word Press. Our look should be very professional and we will be adding Our Team Professional Bios and Headshots.

Industry/Entity Type

Finance

Number of Pages Required

5+ page

Font styles to use
Serif
Sans Serif

Requirements
Must have
• We want to copy quillmorecf.com
• We need:
• Home Page
• About Us
• Loan Programs
• Loan Criteria
• News
• Apply Now
• Contact
Nice to have
• See quillmorecf.com
Should not have
• Need professional design. Nothing bright or abstract

```html
<!DOCTYPE html>
<html lang="en">
<head>
<meta charset="utf-8">
<title>Corvane Lending Partners</title>
<link href="https://fonts.googleapis.com/css2?family=Montserrat:wght@500;600;700&family=Open+Sans:wght@400;600;700&display=swap" rel="stylesheet">
<style>
:root{
  --navy:#1e4d8c;
  --blue:#1f5fa8;
  --stat:#2f86d8;
  --ink:#1a1a1a;
  --text:#333;
  --muted:#666;
  --light:#f3f0ef;
  --white:#fff;
  --rule:#d9d9d9;
}
*{box-sizing:border-box;margin:0;padding:0}
html,body{width:1200px;height:4215px;overflow:hidden;background:var(--white)}
body{position:relative;font-family:"Open Sans",Arial,sans-serif;color:var(--text)}
.abs{position:absolute}
.brand{font-family:"Montserrat",Arial,sans-serif;font-weight:700;color:var(--navy);letter-spacing:.5px}
.site-header .brand{left:145px;top:34px;font-size:30px;line-height:34px;width:280px}
.header-phone{left:700px;top:30px;font-size:13px;color:var(--ink)}
.header-phone strong{display:block;font-size:21px;color:var(--blue);font-weight:700}
.phone-icon{left:695px;top:38px}
.header-follow{left:960px;top:30px;font-size:13px;color:var(--ink)}
.dot{display:inline-block;width:22px;height:22px;border-radius:50%;background:var(--navy);margin-right:4px;margin-top:6px}
.main-nav{left:448px;top:96px;display:flex;gap:0;font-size:13px;font-weight:600;color:var(--ink)}
.main-nav span{padding:0 14px}
.main-nav .active{color:var(--blue);border-bottom:2px solid var(--blue);padding-bottom:6px}
.hero{left:0;top:132px;width:1200px;height:626px;background:linear-gradient(100deg,#2a2420 0%,#4a3d33 40%,#6b5a4a 70%,#3b322c 100%)}
.hero-shade{left:0;top:132px;width:1200px;height:626px;background:linear-gradient(180deg,rgba(0,0,0,0) 40%,rgba(0,0,0,.65) 100%)}
.hero h1{left:175px;top:312px;font-family:"Montserrat",Arial,sans-serif;font-weight:700;color:var(--white);font-size:46px;line-height:56px}
.btn{display:inline-block;background:var(--blue);color:var(--white);font-family:"Montserrat",Arial,sans-serif;font-weight:700;font-size:11px;letter-spacing:.5px;text-transform:uppercase;text-align:center}
.hero .btn-hero{left:178px;top:440px;width:164px;height:48px;line-height:44px;font-size:15px;border:2px solid var(--white)}
.closed-title{left:0;width:1200px;top:598px;text-align:center;color:var(--white);font-family:"Montserrat",Arial,sans-serif;font-weight:700;font-size:17px}
.stats{left:145px;top:648px;width:910px;display:flex;justify-content:space-between;text-align:center;color:var(--white);font-size:11px;line-height:15px}
.stats b{display:block;color:var(--stat);font-size:22px;line-height:28px;font-family:"Montserrat",Arial,sans-serif}
.section-title{left:0;width:1200px;text-align:center;font-family:"Montserrat",Arial,sans-serif;font-weight:700;font-size:31px;color:var(--ink)}
.tile{overflow:hidden}
.tile .label{position:absolute;left:40px;color:var(--white)}
.tile h3{font-family:"Montserrat",Arial,sans-serif;font-weight:700;font-size:19px;margin-bottom:6px}
.tile p{font-size:14px;line-height:18px;font-weight:600;margin-bottom:12px}
.tile .btn{width:100px;height:26px;line-height:26px}
.tile-shade{position:absolute;inset:0;background:linear-gradient(180deg,rgba(0,0,0,0) 45%,rgba(0,0,0,.55) 100%)}
.svc-img{width:305px;height:267px}
.svc-text{width:305px;text-align:center}
.svc-text h4{font-family:"Montserrat",Arial,sans-serif;font-weight:700;font-size:15px;color:var(--ink);margin-bottom:14px}
.svc-text p{font-size:13px;line-height:18px;color:var(--text);padding:0 30px}
.team{left:0;top:3125px;width:1200px;height:725px;background:var(--light)}
.member{width:260px;text-align:center}
.hex{width:210px;height:240px;margin:0 auto;clip-path:polygon(50% 0,100% 25%,100% 75%,50% 100%,0 75%,0 25%)}
.member h5{font-family:"Montserrat",Arial,sans-serif;font-weight:700;font-size:15px;color:var(--ink);margin-top:36px}
.member .role{font-size:12px;font-weight:600;color:var(--ink);margin-top:6px;text-transform:uppercase}
.member p{font-size:13px;line-height:16px;color:var(--muted);margin:18px auto 0;width:200px}
.member .btn{width:126px;height:30px;line-height:30px;margin-top:20px}
.footer .brand{left:165px;top:3938px;font-size:26px;line-height:32px;width:260px}
.foot-col{font-size:12px;line-height:18px;color:var(--text)}
.foot-col h6{font-family:"Montserrat",Arial,sans-serif;font-weight:700;font-size:12px;color:var(--ink);margin-bottom:18px}
.foot-row{display:flex;align-items:flex-start;gap:12px;margin-bottom:16px}
.social-row{display:flex;align-items:center;gap:10px;margin-bottom:14px}
.social-row .dot{margin:0;width:24px;height:24px}
.rule{left:130px;top:4118px;width:940px;height:1px;background:var(--rule)}
.copyright{left:0;width:1200px;top:4168px;text-align:center;font-size:11px;color:var(--text)}
</style>
</head>
<body>

<header class="site-header">
  <div class="abs brand">Corvane Lending Partners</div>
  <svg class="abs phone-icon" width="20" height="20" viewBox="0 0 24 24"><path d="M6.6 10.8a15 15 0 0 0 6.6 6.6l2.2-2.2a1 1 0 0 1 1-.25 11.4 11.4 0 0 0 3.6.57 1 1 0 0 1 1 1V20a1 1 0 0 1-1 1A17 17 0 0 1 3 4a1 1 0 0 1 1-1h3.5a1 1 0 0 1 1 1c0 1.25.2 2.45.57 3.57a1 1 0 0 1-.25 1z" fill="#555"/></svg>
  <div class="abs header-phone" style="left:740px">Call Us now on<strong>555.014.2290</strong></div>
  <div class="abs header-follow">Follow us on<br><span class="dot"></span><span class="dot"></span><span class="dot"></span></div>
  <nav class="abs main-nav"><span class="active">Home</span><span>About Us</span><span>Loan Programs</span><span>Loan Criteria</span><span>News</span><span>Apply Now</span><span>Contact</span></nav>
</header>

<section>
  <div class="abs hero" role="img" aria-label="Smiling business owner in a white shirt standing in a café"></div>
  <div class="abs hero-shade"></div>
  <div class="hero">
    <h1 class="abs">Helping Small<br>Business Owners</h1>
    <span class="abs btn btn-hero">Read More &rsaquo;</span>
  </div>
  <div class="abs closed-title">RECENTLY CLOSED LOANS</div>
  <div class="abs stats">
    <div>Mixed Use<b>$21,000,000</b>Land Development<br>New York, NY</div>
    <div>Mixed Use<b>$3,25,000</b>Refinance<br>New York, NY</div>
    <div>Mixed Use<b>$4,000,000</b>Construction<br>New York, NY</div>
    <div>Mixed Use<b>$12,500,000</b>Property Development<br>New York, NY</div>
    <div>Mixed Use<b>$21,000,000</b>Land Development<br>New York, NY</div>
  </div>
</section>

<section>
  <h2 class="abs section-title" style="top:826px">Loan Programs</h2>
  <div class="abs tile" style="left:0;top:924px;width:765px;height:368px;background:linear-gradient(180deg,#c9d6df 0%,#9fb2b8 30%,#5f7a3a 55%,#4a6a2a 100%)" role="img" aria-label="Green rolling farmland with a dirt road">
    <div class="tile-shade"></div>
    <div class="label" style="top:220px"><h3>LAND LOANS</h3><p>Lorem ipsum dolor sit amet, consectetur adipiscing elit,<br>sed do eiusmod tempor incididunt ut.</p><span class="btn">Read More</span></div>
  </div>
  <div class="abs tile" style="left:765px;top:924px;width:435px;height:368px;background:linear-gradient(160deg,#6b5138 0%,#b08a5c 45%,#d9b98a 70%,#7a5c3e 100%)" role="img" aria-label="Warm-lit hotel lobby with columns">
    <div class="tile-shade"></div>
    <div class="label" style="left:40px;top:222px"><h3>HOSPITALITY LOANS</h3><p>Lorem ipsum dolor sit amet, consectetur adipiscing<br>elit, sed do eiusmod tempor.</p><span class="btn">Read More</span></div>
  </div>
  <div class="abs tile" style="left:0;top:1292px;width:445px;height:368px;background:linear-gradient(170deg,#8fb3d4 0%,#4f7fa8 40%,#2f4f6a 75%,#243a4d 100%)" role="img" aria-label="Glass office towers against a blue sky">
    <div class="tile-shade"></div>
    <div class="label" style="top:226px"><h3>OFFICE LOANS</h3><p>Lorem ipsum dolor sit amet, consectetur adipiscing<br>elit, sed do eiusmod tempor.</p><span class="btn">Read More</span></div>
  </div>
  <div class="abs tile" style="left:445px;top:1292px;width:755px;height:368px;background:linear-gradient(170deg,#b8c4cc 0%,#7d8a92 40%,#4f5a60 75%,#3a4348 100%)" role="img" aria-label="Multistorey apartment buildings">
    <div class="tile-shade"></div>
    <div class="label" style="left:70px;top:226px"><h3>MULTIFAMILY LOANS</h3><p>Lorem ipsum dolor sit amet, consectetur adipiscing elit,<br>sed do eiusmod tempor incididunt ut labore et</p><span class="btn">Read More</span></div>
  </div>
</section>

<section>
  <h2 class="abs section-title" style="top:1716px">Our Services</h2>

  <div class="abs svc-img" style="left:145px;top:1818px;background:linear-gradient(135deg,#5a3a2a,#b07a58 50%,#d8c8b8)" role="img" aria-label="Hands using a tablet at a desk"></div>
  <div class="abs svc-img" style="left:450px;top:1818px;background:linear-gradient(135deg,#3a3a3a,#9a9a9a 50%,#e0e0e0)" role="img" aria-label="Laptop showing a debt consolidation loan form"></div>
  <div class="abs svc-img" style="left:755px;top:1818px;background:linear-gradient(135deg,#e8e8ec,#c8ccd4 50%,#9aa0ac)" role="img" aria-label="Hand signing a document with a pen"></div>
  <div class="abs svc-text" style="left:145px;top:2114px"><h4>WORKING CAPITAL</h4><p>Lorem ipsum dolor sit amet consectetur adipiscing elit, sed do eiusmod.</p></div>
  <div class="abs svc-text" style="left:450px;top:2114px"><h4>DEBT CONSOLIDATIONS</h4><p>Lorem ipsum dolor sit amet consectetur adipiscing elit, sed do eiusmod.</p></div>
  <div class="abs svc-text" style="left:755px;top:2114px"><h4>PAYROLL</h4><p>Lorem ipsum dolor sit amet consectetur adipiscing elit, sed do eiusmod.</p></div>

  <div class="abs svc-img" style="left:145px;top:2238px;background:linear-gradient(135deg,#c0a080,#e8dcc8 50%,#8a6a50)" role="img" aria-label="Team reviewing financial charts on a table"></div>
  <div class="abs svc-img" style="left:450px;top:2238px;background:linear-gradient(180deg,#f0ede6,#b8a890 50%,#6a5a48)" role="img" aria-label="Warehouse aisle with stocked shelves"></div>
  <div class="abs svc-img" style="left:755px;top:2238px;background:linear-gradient(135deg,#0c1a2e,#1e3a5a 50%,#0a1424)" role="img" aria-label="Hands cupped around a glowing dollar symbol"></div>
  <div class="abs svc-text" style="left:145px;top:2533px"><h4>OPERATING EXPENSES</h4><p>Lorem ipsum dolor sit amet consectetur adipiscing elit, sed do eiusmod.</p></div>
  <div class="abs svc-text" style="left:450px;top:2533px"><h4>INVENTORY</h4><p>Lorem ipsum dolor sit amet consectetur adipiscing elit, sed do eiusmod.</p></div>
  <div class="abs svc-text" style="left:755px;top:2533px"><h4>EQUIPMENT FINANCING</h4><p>Lorem ipsum dolor sit amet consectetur adipiscing elit, sed do eiusmod.</p></div>

  <div class="abs svc-img" style="left:145px;top:2658px;background:linear-gradient(180deg,#5a8ac4,#a8c4e0 45%,#8a7a66 75%,#5a4a3a)" role="img" aria-label="Commercial building under a blue sky"></div>
  <div class="abs svc-img" style="left:450px;top:2658px;background:linear-gradient(135deg,#2a4a6a,#6a8aa8 50%,#c8d4de)" role="img" aria-label="Business people shaking hands in an office"></div>
  <div class="abs svc-img" style="left:755px;top:2658px;background:linear-gradient(135deg,#0a1830,#1e3c6a 50%,#0c1a34)" role="img" aria-label="Businessman facing a starry blue horizon"></div>
  <div class="abs svc-text" style="left:145px;top:2952px"><h4>COMMERCIAL REAL ESTATE</h4><p>Lorem ipsum dolor sit amet consectetur adipiscing elit, sed do eiusmod.</p></div>
  <div class="abs svc-text" style="left:450px;top:2952px"><h4>BUSINESS ACQUISITIONS</h4><p>Lorem ipsum dolor sit amet consectetur adipiscing elit, sed do eiusmod.</p></div>
  <div class="abs svc-text" style="left:755px;top:2952px"><h4>BUSINESS EXPANSION</h4><p>Lorem ipsum dolor sit amet consectetur adipiscing elit, sed do eiusmod.</p></div>
</section>

<section>
  <div class="abs team"></div>
  <h2 class="abs section-title" style="top:3182px">Our Team</h2>
  <svg class="abs" style="left:80px;top:3410px" width="20" height="30" viewBox="0 0 20 30"><path d="M15 3 4 15l11 12" fill="none" stroke="#999" stroke-width="2"/></svg>
  <svg class="abs" style="left:1080px;top:3410px" width="20" height="30" viewBox="0 0 20 30"><path d="M5 3l11 12L5 27" fill="none" stroke="#999" stroke-width="2"/></svg>
  <div class="abs member" style="left:150px;top:3300px"><div class="hex" style="background:linear-gradient(180deg,#d8d4cc,#6a6a6a 60%,#2a2a30)" role="img" aria-label="Headshot of Daniel, CEO"></div><h5>DANIEL</h5><div class="role">CEO</div><p>There are many variations of passages of Lorem Ipsum available, but the majority have suffered alteration in some form, by injected humour, or randomised</p><span class="btn">View Profile</span></div>
  <div class="abs member" style="left:470px;top:3300px"><div class="hex" style="background:linear-gradient(180deg,#e4e4e4,#8a8a8a 60%,#2a2a2a)" role="img" aria-label="Headshot of Clara Hughes, accounting manager"></div><h5>CLARA HUGHES</h5><div class="role">Accounting Manger</div><p>There are many variations of passages of Lorem Ipsum available, but the majority have suffered alteration in some form, by injected humour, or randomised</p><span class="btn">View Profile</span></div>
  <div class="abs member" style="left:783px;top:3300px"><div class="hex" style="background:linear-gradient(180deg,#ececec,#9a9a9a 60%,#3a3a40)" role="img" aria-label="Headshot of Owen Pryce, employee"></div><h5>OWEN PRYCE</h5><div class="role">Employee</div><p>There are many variations of passages of Lorem Ipsum available, but the majority have suffered alteration in some form, by injected humour, or randomised</p><span class="btn">View Profile</span></div>
</section>

<footer class="footer">
  <div class="abs brand">Corvane Lending Partners</div>
  <div class="abs foot-col" style="left:515px;top:3895px">
    <h6>CONTACT US</h6>
    <div class="foot-row"><svg width="12" height="14" viewBox="0 0 24 24"><path d="M12 2a7 7 0 0 0-7 7c0 5 7 13 7 13s7-8 7-13a7 7 0 0 0-7-7zm0 9.5A2.5 2.5 0 1 1 12 6.5a2.5 2.5 0 0 1 0 5z" fill="#333"/></svg><span>118 Foundry Lane<br>Ashby, IL 60517</span></div>
    <div class="foot-row"><svg width="12" height="12" viewBox="0 0 24 24"><path d="M6.6 10.8a15 15 0 0 0 6.6 6.6l2.2-2.2a1 1 0 0 1 1-.25 11.4 11.4 0 0 0 3.6.57 1 1 0 0 1 1 1V20a1 1 0 0 1-1 1A17 17 0 0 1 3 4a1 1 0 0 1 1-1h3.5a1 1 0 0 1 1 1c0 1.25.2 2.45.57 3.57a1 1 0 0 1-.25 1z" fill="#333"/></svg><span>555.014.2290</span></div>
    <div class="foot-row"><svg width="12" height="12" viewBox="0 0 24 24"><path d="M2 5h20v14H2zm2 2v.5l8 5 8-5V7z" fill="#333"/></svg><span>info@corvanelending.com</span></div>
  </div>
  <div class="abs foot-col" style="left:748px;top:3895px">
    <h6>MENU</h6>
    Home<br>About Us<br>Loan Programs<br>Loan Criteria<br>News<br>Apply Now<br>Contact
  </div>
  <div class="abs foot-col" style="left:937px;top:3895px">
    <h6>CONNECT WITH US</h6>
    <div class="social-row"><span class="dot"></span>Feed</div>
    <div class="social-row"><span class="dot"></span>Updates</div>
    <div class="social-row"><span class="dot"></span>Network</div>
  </div>
  <div class="abs rule"></div>
  <div class="abs copyright">Copyrights © 2018 All Rights Reserved</div>
</footer>

</body>
</html>
```